BOLD & MINIMALIST DESIGN NEEDED

We want a very bold but minimalistic business card design that is impactful and utilizes both sides of the business card. Our current logo is included for your use.

We want bold fonts and good use of negative space. We don't want the logo to overpower the design.

Target Market(s)

Professionals who are building new commercial buildings.

Industry/Entity Type

Construction

Contact Information for Business Card

Name, Title, email, office phone, cell phone, website

Font styles to use
Serif
Sans Serif

Requirements
Must have
• Bold design!

```html
<!DOCTYPE html>
<html lang="en">
<head>
<meta charset="utf-8">
<title>Summitline Design + Build — Business Card</title>
<link rel="stylesheet" href="https://fonts.googleapis.com/css2?family=Montserrat:wght@700&family=Roboto:wght@500;700;900&display=swap">
<style>
  :root {
    --backdrop: #dfe4e2;
    --card: #ffffff;
    --ink: #111111;
    --text-grey: #555555;
    --accent: #7cc242;
  }
  * { margin: 0; padding: 0; box-sizing: border-box; }
  html, body {
    width: 1200px;
    height: 716px;
    overflow: hidden;
    background: var(--backdrop);
  }
  .canvas {
    position: relative;
    width: 1200px;
    height: 716px;
  }
  .card {
    position: absolute;
    left: 369px;
    width: 461px;
    height: 263px;
    background: var(--card);
    border-radius: 12px;
    box-shadow: -2px 2px 0 var(--ink);
  }
  .card--front { top: 94px; }
  .card--back { top: 382px; }

  .wordmark {
    display: flex;
    align-items: center;
    gap: 8px;
    font-family: "Roboto", sans-serif;
    font-weight: 900;
    color: var(--ink);
    text-transform: uppercase;
    white-space: nowrap;
  }
  .wordmark__square {
    background: var(--accent);
    flex: none;
  }
  .card--front .wordmark {
    position: absolute;
    left: 50%;
    top: 50%;
    transform: translate(-50%, -50%);
    font-size: 22px;
    letter-spacing: 0.5px;
  }
  .card--front .wordmark__square { width: 22px; height: 22px; }

  .card--back .wordmark {
    position: absolute;
    left: 19px;
    top: 30px;
    font-size: 12px;
  }
  .card--back .wordmark__square { width: 12px; height: 12px; }

  .person {
    position: absolute;
    right: 16px;
    top: 22px;
    text-align: right;
    color: var(--text-grey);
  }
  .person__name {
    font-family: "Montserrat", sans-serif;
    font-weight: 700;
    font-size: 15px;
    line-height: 18px;
  }
  .person__title {
    font-family: "Roboto", sans-serif;
    font-weight: 700;
    font-size: 12px;
    line-height: 16px;
    margin-top: 2px;
  }

  .contact {
    position: absolute;
    left: 19px;
    top: 179px;
    list-style: none;
    font-family: "Roboto", sans-serif;
    font-weight: 700;
    font-size: 12.8px;
    line-height: 16.7px;
    color: var(--text-grey);
    white-space: nowrap;
  }
</style>
</head>
<body>
<main class="canvas">
  <section class="card card--front" aria-label="Card front">
    <div class="wordmark">
      <span class="wordmark__square"></span>
      <span class="wordmark__name">Summitline Design + Build</span>
    </div>
  </section>

  <section class="card card--back" aria-label="Card back">
    <div class="wordmark">
      <span class="wordmark__square"></span>
      <span class="wordmark__name">Summitline Design + Build</span>
    </div>

    <div class="person">
      <p class="person__name">DANA WHITFIELD</p>
      <p class="person__title">Designer</p>
    </div>

    <ul class="contact">
      <li>+1-555-014-2290</li>
      <li>hello@summitline.co</li>
      <li>www.summitline.co</li>
      <li>48 Ridgeview Road &nbsp;| Suite 210, Denver CO</li>
    </ul>
  </section>
</main>
</body>
</html>
```